A Health & Fitness Website selling saunas and Cold tubs

www.dockvaultguys.com, www.frostlanterguys, www.chillharborguys
Design a website
We are selling saunas, infrared saunas, cold plunge tubs, and massage chairs to financially successful MEN.
We want professional, simple, masculine with a touch of sexy.
One section for each… saunas, cold plunge tubs, massage chairs.
Each will have at least two buy links to their affiliate/supplier/store.
The landing page / opening page / needs big & bold; a full screen image? a great picture showing the warmth of a sauna? Need your ideas
The pictures are everything.

The Website for our book
https://maebelsvigorguys.com/

Coding

Coded - Design and coding required

Number of Pages Required

1 page

Requirements
Must have
• Great pictures

```html
<!DOCTYPE html>
<html lang="en">
<head>
<meta charset="UTF-8">
<title>Maebel Vigor – Saunas, Cold Plunge Tubs & Massage Chairs</title>
<link rel="stylesheet" href="https://fonts.googleapis.com/css2?family=Oswald:wght@400;500&family=Poppins:wght@400;500&display=swap">
<style>
:root{
  --orange:#eb6f24;
  --orange-deep:#c9561a;
  --black:#000;
  --ink:#1b1b1b;
  --white:#fff;
  --grey-text:#333;
  --wood-dark:#3a1d0c;
  --wood-mid:#8a4b22;
  --wood-light:#c98a4d;
}
*{margin:0;padding:0;box-sizing:border-box}
html,body{width:1200px;height:4662px;overflow:hidden;background:var(--white)}
body{position:relative;font-family:'Poppins',sans-serif;color:var(--ink)}
.abs{position:absolute}
.display{font-family:'Oswald',sans-serif;font-weight:500;text-transform:uppercase}
.accent{color:var(--orange)}

/* brand mark */
.brand{position:absolute;left:50%;transform:translateX(-50%);width:180px;height:180px;border-radius:50%;background:var(--black);display:flex;align-items:center;justify-content:center;text-align:center;font-family:'Oswald',sans-serif;font-weight:500;color:var(--white);font-size:24px;line-height:1.15;letter-spacing:1px;text-transform:uppercase;z-index:5}
.brand-top{top:9px}
.brand-foot{top:4415px;width:170px;height:170px}

/* hero */
.hero{top:97px;left:0;width:1200px;height:640px}
.hero-photo{position:absolute;inset:0;background:linear-gradient(90deg,#050302 0%,#1a0c05 32%,var(--wood-dark) 50%,var(--wood-mid) 75%,var(--wood-light) 100%)}
.hero-curve{position:absolute;left:0;top:0;width:1200px;height:640px}
.hero-title{left:68px;top:268px;font-size:46px;line-height:70px;color:var(--white);z-index:2}
.hero-sub{left:68px;top:424px;font-size:16px;line-height:34px;color:var(--white);z-index:2}

/* product rows */
.photo{position:absolute}
.photo-sauna{left:114px;top:822px;width:592px;height:508px;background:linear-gradient(120deg,#3b1c0a,#9a5a25 55%,#d9a066)}
.photo-plunge{left:494px;top:1379px;width:592px;height:509px;background:linear-gradient(180deg,#c9dbe8 0%,#5a8aa6 45%,#0e2433 70%,#e8f1f7 100%)}
.photo-chair{left:114px;top:1935px;width:592px;height:510px;background:linear-gradient(110deg,#1c1c1c 0%,#4a4a4a 40%,#d8d4cf 75%,#f2efea 100%)}
.card{position:absolute;width:433px;height:378px;background:var(--orange);color:var(--white);text-align:center;padding-top:18px;z-index:2}
.card-sauna{left:653px;top:887px}
.card-plunge{left:114px;top:1443px}
.card-chair{left:653px;top:2000px}
.card-fold{position:absolute;left:494px;top:1822px;width:0;height:0;border-top:24px solid var(--orange-deep);border-right:51px solid transparent;z-index:2}
.card-icon{width:90px;height:90px;margin:0 auto}
.card h2{font-size:25px;margin-top:22px;letter-spacing:.3px}
.card p{font-size:16px;line-height:36px;margin-top:12px;padding:0 30px}
.card-actions{display:flex;justify-content:center;gap:20px;margin-top:16px}
.btn{display:inline-block;width:130px;height:42px;line-height:42px;border-radius:21px;background:var(--black);color:var(--white);font-family:'Oswald',sans-serif;font-size:16px;text-transform:uppercase;text-decoration:none}

/* banner */
.banner{top:2516px;left:0;width:1200px;height:574px}
.banner-photo{position:absolute;left:0;top:30px;width:1200px;height:544px;background:linear-gradient(90deg,#7a3f18 0%,#b9733a 35%,#6a3414 62%,#1a0a03 82%,#000 100%)}
.banner-arc{position:absolute;left:0;top:0;width:1200px;height:140px}
.banner-title{right:87px;top:2860px;text-align:right;font-size:46px;line-height:70px;color:var(--white);z-index:2}

/* benefits */
.benefits-head{left:0;width:1200px;text-align:center}
.bh-1{top:3168px;font-size:32px;color:var(--ink)}
.bh-2{top:3220px;font-size:32px;color:var(--orange)}
.bh-sub{top:3288px;font-size:16px;line-height:36px;color:var(--grey-text)}
.tag{position:absolute;height:62px;border:2px solid var(--orange);font-family:'Oswald',sans-serif;font-size:21px;color:var(--ink);display:flex;align-items:center;justify-content:center;white-space:nowrap}
.bh-note{top:3720px;font-size:24px;color:var(--ink)}

/* testimonials */
.testi-title{top:3830px;font-size:32px;color:var(--orange)}
.quote{position:absolute;top:3928px;width:429px;height:322px;background:var(--white);box-shadow:0 2px 10px rgba(0,0,0,.18);text-align:center;font-size:16px;line-height:35.5px;color:var(--grey-text);padding:43px 8px 0}
.q1{left:163px}.q2{left:610px}
.avatar{position:absolute;top:4200px;width:96px;height:96px;border-radius:50%;border:3px solid var(--white);z-index:2}
.av1{left:330px;background:linear-gradient(180deg,#7ec8e3,#e46b2a)}
.av2{left:777px;background:linear-gradient(180deg,#e9e9e9,#222)}
.arrow{position:absolute;top:4063px;width:38px;height:38px;border-radius:50%}
.arrow-prev{left:82px;background:var(--black)}
.arrow-next{left:1081px;background:var(--orange)}

/* footer */
.footer{top:4382px;left:0;width:1200px;height:280px;background:var(--black)}
.copyright{left:0;top:4612px;width:1200px;text-align:center;color:var(--white);font-size:16px;z-index:2}
</style>
</head>
<body>

<div class="brand brand-top">Maebel<br>Vigor</div>

<section class="abs hero">
  <div class="hero-photo" role="img" aria-label="Woman in a white robe and towel relaxing in a warm wooden sauna"></div>
  <svg class="hero-curve" viewBox="0 0 1200 640" aria-hidden="true">
    <path d="M0 518 Q600 740 1200 518 L1200 640 L0 640 Z" fill="#fff"/>
    <path d="M105 555 Q600 700 1200 520 Q620 735 105 555 Z" fill="#eb6f24"/>
  </svg>
</section>
<h1 class="abs display hero-title">Dramatically Improve Your<br>Health&nbsp; <span class="accent">Without Exercise</span></h1>
<p class="abs hero-sub">Successful Men Recognize the Importance of Their Health<br>and Make it a Priority.&nbsp; It's Your Time.&nbsp; You've Earned it.</p>

<!-- Saunas -->
<div class="photo photo-sauna" role="img" aria-label="Couple relaxing in a candle-lit sauna"></div>
<article class="card card-sauna">
  <svg class="card-icon" viewBox="0 0 90 90" fill="none" stroke="#fff" stroke-width="3" aria-hidden="true">
    <path d="M18 30 H72 L66 80 H24 Z"/><path d="M20 45 H70 M22 62 H68"/><path d="M34 30 V80 M46 30 V80 M58 30 V80"/><path d="M40 30 L62 8"/><circle cx="64" cy="70" r="8"/>
  </svg>
  <h2 class="display">Saunas</h2>
  <p>Sed ut perspiciatis unde omnis iste natus error sit voluptatem accusantium doloremque laudantium.</p>
  <div class="card-actions"><a class="btn" href="#">Shop Now</a><a class="btn" href="#">Buy Now</a></div>
</article>

<!-- Cold plunge -->
<div class="photo photo-plunge" role="img" aria-label="Two people splashing in an icy cold plunge pool"></div>
<article class="card card-plunge">
  <svg class="card-icon" viewBox="0 0 90 90" fill="none" stroke="#fff" stroke-width="3" aria-hidden="true">
    <path d="M32 8 q-4 5 0 10 q4 5 0 10 M45 8 q-4 5 0 10 q4 5 0 10 M58 8 q-4 5 0 10 q4 5 0 10"/>
    <ellipse cx="45" cy="44" rx="30" ry="8"/><path d="M15 44 V72 Q45 86 75 72 V44"/><path d="M25 50 V76 M35 52 V79 M45 52 V80 M55 52 V79 M65 50 V76"/>
  </svg>
  <h2 class="display">Cold Plunge Tubs</h2>
  <p>Sed ut perspiciatis unde omnis iste natus error sit voluptatem accusantium doloremque laudantium.</p>
  <div class="card-actions"><a class="btn" href="#">Shop Now</a><a class="btn" href="#">Buy Now</a></div>
</article>
<div class="card-fold"></div>

<!-- Massage chairs -->
<div class="photo photo-chair" role="img" aria-label="Woman resting in a reclined massage chair"></div>
<article class="card card-chair">
  <svg class="card-icon" viewBox="0 0 90 90" fill="none" stroke="#fff" stroke-width="3" aria-hidden="true">
    <path d="M22 10 L40 48 L70 50 L72 62 L44 64 Z"/><path d="M30 8 q6 -4 8 4"/><path d="M50 64 V76 M32 80 H68"/><path d="M56 30 q6 4 0 8 M64 28 q8 6 0 12"/>
  </svg>
  <h2 class="display">Massage Chairs</h2>
  <p>Sed ut perspiciatis unde omnis iste natus error sit voluptatem accusantium doloremque laudantium.</p>
  <div class="card-actions"><a class="btn" href="#">Shop Now</a><a class="btn" href="#">Buy Now</a></div>
</article>

<!-- Banner -->
<section class="abs banner">
  <div class="banner-photo" role="img" aria-label="Couple sitting together on a wooden sauna bench"></div>
  <svg class="banner-arc" viewBox="0 0 1200 140" aria-hidden="true">
    <path d="M0 0 H1200 V120 Q600 -40 0 120 Z" fill="#fff"/>
    <path d="M25 100 Q560 -45 1095 70 Q560 -25 25 100 Z" fill="#eb6f24"/>
  </svg>
</section>
<h2 class="abs display banner-title">Everything Works Better<br>with Increased <span class="accent">Blood Flow</span></h2>

<!-- Benefits -->
<h2 class="abs display benefits-head bh-1">A Mans Body Thrives on Circulation&nbsp; &amp; It Doesn't Care</h2>
<h3 class="abs display benefits-head bh-2">How You Get It</h3>
<p class="abs benefits-head bh-sub">When there's no time for exercise.&nbsp; use Hot, Cold, or Massage.<br>The Benefits are Numerous.</p>

<div class="tag" style="left:112px;top:3388px;width:181px">Relieve Stress</div>
<div class="tag" style="left:309px;top:3388px;width:180px">Detox Your Pores</div>
<div class="tag" style="left:507px;top:3388px;width:336px">Sleep Better Relieve Muscle Tension</div>
<div class="tag" style="left:858px;top:3388px;width:228px">Reduce Inflammation</div>
<div class="tag" style="left:112px;top:3466px;width:378px">Boost Energy Levels Increase Testosterone</div>
<div class="tag" style="left:505px;top:3466px;width:338px">Increase Immunity&nbsp; Reduce Depression</div>
<div class="tag" style="left:858px;top:3466px;width:228px">Alleviate Joint Pain</div>
<div class="tag" style="left:112px;top:3544px;width:487px">Healthier Skin Lower the Risk of Cardiovascular Disease</div>
<div class="tag" style="left:613px;top:3544px;width:473px">Increase Metabolism Promote Weight Loss</div>
<div class="tag" style="left:440px;top:3622px;width:320px">A Longer &amp; Healthier Life</div>

<p class="abs display benefits-head bh-note" style="font-weight:400">Specific Improvements Will Be Individual to You.</p>

<!-- Testimonials -->
<h2 class="abs display benefits-head testi-title">Testimonials</h2>
<blockquote class="quote q1">"I climb in my sauna half asleep every morning for 20 minutes before I take a shower and head off to work. It's the only thing I found that really wakes me up in the morning. I'm not a coffee drinker so that's never been an option but this sauna is the perfect morning wake up."</blockquote>
<blockquote class="quote q2">"Having a sauna in my home has been a game-changer. After a long day at work, I step into warmth and it's total relaxation. The heat and gentle steam instantly melts me. It's like a mini vacation without leaving home. I can't imagine life without my sauna."</blockquote>
<div class="avatar av1" role="img" aria-label="Customer portrait"></div>
<div class="avatar av2" role="img" aria-label="Customer portrait"></div>
<a class="arrow arrow-prev" href="#" aria-label="Previous">
  <svg viewBox="0 0 38 38" width="38" height="38" aria-hidden="true"><path d="M22 12 L15 19 L22 26" fill="none" stroke="#fff" stroke-width="3.5" stroke-linecap="round" stroke-linejoin="round"/></svg>
</a>
<a class="arrow arrow-next" href="#" aria-label="Next">
  <svg viewBox="0 0 38 38" width="38" height="38" aria-hidden="true"><path d="M16 12 L23 19 L16 26" fill="none" stroke="#fff" stroke-width="3.5" stroke-linecap="round" stroke-linejoin="round"/></svg>
</a>

<!-- Footer -->
<footer class="abs footer"></footer>
<div class="brand brand-foot">Maebel<br>Vigor</div>
<p class="abs copyright">@2024 Copyrights. All Rights Reserved</p>

</body>
</html>
```